BrindleStaffing Business Card Design

We are a staffing company finding positions for dedicated nurses and physicians.

Target Market(s)

Business Professionals

Industry/Entity Type

Staffing

Contact Information for Business Card

Gordon Pratley
Chairman
417 39th Avenue South
SAINT PETERSBURG FL 33712
813-555-4172 Mobile
813-555-8036 Fax
gpratley@brindlestaffing.com
www.brindlestaffing.com

Font styles to use
Sans Serif

Colors
fbee3e
f04a50
f37122

Requirements
Must have
• Logo Attached, see colors below. We'd like to see Yellow, Orange and Red.

```html
<!DOCTYPE html>
<html lang="en">
<head>
<meta charset="utf-8">
<title>BrindleStaffing Business Card</title>
<link href="https://fonts.googleapis.com/css2?family=Nunito:wght@600;700&family=Lato:wght@400&display=swap" rel="stylesheet">
<style>
  :root {
    --backdrop: #4d4d4d;
    --card-white: #ffffff;
    --brand-yellow: #fbee3e;
    --brand-orange: #f37122;
    --brand-red: #f04a50;
    --ink: #2b2b2b;
    --muted: #6a6a6a;
  }
  * { margin: 0; padding: 0; box-sizing: border-box; }
  html, body { width: 1200px; height: 802px; overflow: hidden; }
  body { background: var(--backdrop); position: relative; }
  .card {
    position: absolute;
    top: 274px;
    width: 443px;
    height: 265px;
    box-shadow: 3px 4px 8px rgba(0,0,0,0.45);
    overflow: hidden;
  }
  .card-front { left: 136px; background: var(--card-white); }
  .card-back {
    left: 624px;
    background: linear-gradient(to bottom, var(--brand-red) 0%, var(--brand-orange) 55%, var(--brand-yellow) 100%);
  }
  .side-band {
    position: absolute; left: 0; top: 0; bottom: 0;
    width: 48px; background: var(--brand-orange);
  }
  .side-stripe {
    position: absolute; left: 48px; top: 0; bottom: 0;
    width: 4px; background: var(--brand-red);
  }
  .wordmark {
    position: absolute;
    font-family: "Nunito", sans-serif;
    font-weight: 700;
    letter-spacing: -0.3px;
    white-space: nowrap;
  }
  .card-front .wordmark {
    right: 45px; top: 50px;
    font-size: 25px;
    color: var(--brand-orange);
  }
  .card-back .wordmark {
    left: 0; right: 0; top: 113px;
    text-align: center;
    font-size: 32px;
    color: var(--card-white);
  }
  .person-name {
    position: absolute; left: 78px; top: 112px;
    font-family: "Nunito", sans-serif;
    font-weight: 600;
    font-size: 19px;
    line-height: 24px;
  }
  .first-name { color: var(--brand-red); }
  .last-name { color: var(--brand-orange); }
  .job-title {
    position: absolute; left: 79px; top: 136px;
    font-family: "Lato", sans-serif;
    font-size: 11.5px;
    color: var(--muted);
    letter-spacing: 0.3px;
  }
  .contact-list {
    position: absolute; left: 78px; top: 156px;
    list-style: none;
    font-family: "Lato", sans-serif;
    font-size: 12.5px;
    color: var(--ink);
    line-height: 15px;
  }
  .contact-list li { display: flex; align-items: center; gap: 4px; white-space: nowrap; }
  .contact-list svg { width: 10px; height: 10px; fill: var(--brand-orange); flex: none; }
  .address {
    position: absolute; left: 79px; top: 220px;
    font-family: "Lato", sans-serif;
    font-size: 12.5px;
    color: var(--ink);
    line-height: 15px;
    font-style: normal;
    white-space: nowrap;
  }
</style>
</head>
<body>
  <section class="card card-front">
    <div class="side-band"></div>
    <div class="side-stripe"></div>
    <div class="wordmark">BrindleStaffing</div>
    <h1 class="person-name"><span class="first-name">Gordon</span> <span class="last-name">Pratley</span></h1>
    <p class="job-title">Chairman</p>
    <ul class="contact-list">
      <li><svg viewBox="0 0 10 10" aria-hidden="true"><path d="M1 3.5C1 2 2.5 1.5 5 1.5S9 2 9 3.5L7.5 4 7 3H3L2.5 4ZM2.5 5 3.5 4h3l1 1v3.5h-5Z"/></svg>813-555-4172 Mobile</li>
      <li><svg viewBox="0 0 10 10" aria-hidden="true"><path d="M2.5 0.8h5v2.4h-5Z M0.8 3.6h8.4v4h-1.6v-1.6h-5.2v1.6h-1.6Z M3 6.6h4v2.6h-4Z"/></svg>813-555-8036 Fax</li>
      <li><svg viewBox="0 0 10 10" aria-hidden="true"><path d="M0.5 2h9v6.5h-9Z M1.2 2.6 5 5.6 8.8 2.6" stroke="#fff" stroke-width="0.8"/></svg>gpratley@brindlestaffing.com</li>
      <li><svg viewBox="0 0 10 10" aria-hidden="true"><circle cx="5" cy="5" r="4.5"/><path d="M3 3.2 4.8 2.8 5.5 4.5 4 5.5 4.5 7.5 3 6.5Z M6.5 6 7.8 5.5 7.5 7.5Z" fill="#fff"/></svg>www.brindlestaffing.com</li>
    </ul>
    <address class="address">417 39th Avenue South<br>SAINT PETERSBURG FL 33712</address>
  </section>
  <section class="card card-back">
    <div class="wordmark">BrindleStaffing</div>
  </section>
</body>
</html>
```